Cover für Hauptkatalog
Kompetenter Kontakt. Super schnell wurden die Änderungswünsche umgesetzt. Vielen Dank und bis zum nächsten Mal.
Zielgruppe
BASTUVO GmbH ist ein führender Großhändler in der Hobby- und Bastelbranche. mit unseren weit über 8.000 Produkten beliefern wir Einzelhändler in ganz Europa. Durch unsere Größe sind wir in der Lage sehr schnell auf individuelle Kundenwünsche zu reagieren.
Aufgabenstellung
Wir werden Mitte Dezember einen neuen Kreativ-Katalog mit über 450 Seiten unseren Kunden zur Verfügung stellen. In diesem Zusammenhang soll der Umschlag (Vorder- und Rückseite) in einem neuen, frischen Design erscheinen. Das aktuelle Layout kann unter www.bastuvo-beispiel.com eingesehen werden. Auf der Rückseite soll unsere Adresse stehen.

```html
<!DOCTYPE html>
<html lang="de">
<head>
<meta charset="utf-8">
<title>Freude an Kreativität – Katalogumschlag</title>
<link rel="stylesheet" href="https://fonts.googleapis.com/css2?family=Bungee&family=Caveat:wght@500&family=Montserrat:wght@500;600;700&display=swap">
<style>
  :root {
    --page: #ffffff;
    --lilac-light: #e6cde3;
    --lilac-pale: #f3e6ef;
    --purple-deep: #7a4b90;
    --purple-mid: #8a5a9d;
    --purple-blob: #76468b;
    --cyan: #29a8d1;
    --white: #ffffff;
    --dash: rgba(240, 190, 220, 0.7);
    --brand-blue: #22318a;
  }
  * { box-sizing: border-box; margin: 0; padding: 0; }
  html, body { width: 839px; height: 1200px; overflow: hidden; background: var(--page); }
  .spread {
    position: absolute; left: 30px; top: 337px; width: 779px; height: 525px;
    background: linear-gradient(90deg, var(--lilac-light) 0%, var(--lilac-pale) 100%);
    overflow: hidden;
    font-family: "Montserrat", sans-serif;
  }
  .panel {
    position: absolute; left: 19px; top: 19px; width: 734px; height: 440px;
    border-radius: 20px;
    background: linear-gradient(90deg, var(--purple-deep) 0%, var(--purple-mid) 100%);
  }
  .blobs { position: absolute; inset: 0; }
  .doodle {
    position: absolute; border: 1px dashed var(--dash); border-radius: 40%;
    background: rgba(255,255,255,0.04);
  }
  .photo-strip {
    position: absolute; left: 0; top: 139px; width: 334px; height: 80px;
    display: flex; outline: 1px dashed var(--dash); outline-offset: 3px;
  }
  .photo-strip .photo { height: 100%; }
  .photo--candles { width: 86px; background: linear-gradient(135deg, #9fd7e0, #f4f0ec 60%, #8fc8d6); }
  .photo--pinwheels { width: 122px; background: linear-gradient(120deg, #f08a3a, #d16ac8 45%, #7fb3e8 70%, #e8e04a); }
  .photo--owl { width: 126px; background: linear-gradient(90deg, #cfe2d6, #3fa6c4 55%, #e987b0); }
  .web {
    position: absolute; left: 200px; top: 229px; width: 130px; text-align: center;
    color: var(--white); font-size: 9px; font-weight: 500; letter-spacing: 1px;
  }
  .spine {
    position: absolute; left: 357px; top: 435px; width: 310px; height: 46px;
    transform-origin: 0 0; transform: rotate(-90deg);
    display: flex; align-items: center; gap: 12px;
  }
  .spine .title { font-size: 34px; }
  .spine .subtitle { font-size: 34px; }
  .title {
    font-family: "Bungee", sans-serif; color: var(--white); line-height: 1;
    text-shadow: 2px 2px 0 var(--cyan), 3px 3px 0 var(--cyan);
    -webkit-text-stroke: 1px var(--cyan);
  }
  .subtitle { font-family: "Caveat", cursive; color: var(--white); line-height: 1; }
  .front-title {
    position: absolute; left: 441px; top: 136px; width: 294px; height: 86px;
    border: 1px dashed var(--dash); border-radius: 6px;
    display: flex; align-items: center; justify-content: center;
  }
  .front-title .title { font-size: 66px; letter-spacing: -1px; }
  .front-subtitle { position: absolute; left: 545px; top: 222px; font-size: 38px; }
  .tagline {
    position: absolute; left: 545px; top: 397px;
    color: var(--white); font-size: 10.5px; font-weight: 600; letter-spacing: 1px; line-height: 15px;
  }
  .brand {
    position: absolute; top: 480px; display: flex; align-items: center; gap: 4px;
    color: var(--brand-blue); font-weight: 700; font-size: 14px; letter-spacing: -0.3px;
  }
  .brand .mark { width: 9px; height: 9px; background: #d9232e; }
  .brand--back { left: 20px; }
  .brand--front { left: 666px; }
  .address {
    position: absolute; left: 116px; top: 482px;
    color: var(--brand-blue); font-size: 5px; font-weight: 700; line-height: 7px; letter-spacing: .3px;
  }
</style>
</head>
<body>
  <main class="spread">
    <div class="panel"></div>

    <svg class="blobs" width="779" height="525" viewBox="0 0 779 525" aria-hidden="true">
      <path d="M320 30 C 360 -5, 470 -10, 520 60 C 560 120, 500 160, 430 150 C 360 140, 300 90, 320 30 Z" fill="rgba(0,0,0,0.06)"/>
      <path d="M420 420 C 440 340, 560 300, 640 330 C 700 355, 720 420, 700 525 L 430 525 C 400 490, 410 450, 420 420 Z" fill="var(--purple-blob)" opacity="0.7"/>
      <path d="M160 260 C 200 240, 260 270, 250 330 C 240 390, 180 420, 140 390 C 110 360, 120 290, 160 260 Z" fill="rgba(0,0,0,0.05)"/>
    </svg>

    <div class="doodle" style="left:45px;top:65px;width:60px;height:60px" role="img" aria-label="Line doodle of a light bulb"></div>
    <div class="doodle" style="left:220px;top:80px;width:42px;height:48px" role="img" aria-label="Line doodle of a push pin"></div>
    <div class="doodle" style="left:375px;top:8px;width:115px;height:70px" role="img" aria-label="Line doodle of a paintbrush"></div>
    <div class="doodle" style="left:600px;top:75px;width:50px;height:55px" role="img" aria-label="Line doodle of a thread spool"></div>
    <div class="doodle" style="left:710px;top:30px;width:69px;height:80px" role="img" aria-label="Line doodle of a pencil"></div>
    <div class="doodle" style="left:420px;top:240px;width:105px;height:55px" role="img" aria-label="Line doodle of a rolled scroll with a bow"></div>
    <div class="doodle" style="left:690px;top:255px;width:89px;height:75px" role="img" aria-label="Line doodle of scissors"></div>
    <div class="doodle" style="left:140px;top:285px;width:55px;height:50px" role="img" aria-label="Line doodle of an eraser"></div>
    <div class="doodle" style="left:300px;top:310px;width:65px;height:60px" role="img" aria-label="Line doodle of a paint palette"></div>
    <div class="doodle" style="left:125px;top:385px;width:90px;height:75px" role="img" aria-label="Line doodle of a heart"></div>
    <div class="doodle" style="left:0;top:310px;width:45px;height:80px" role="img" aria-label="Line doodle of a flower pot"></div>
    <div class="doodle" style="left:265px;top:440px;width:70px;height:70px" role="img" aria-label="Line doodle of a pincushion"></div>
    <div class="doodle" style="left:510px;top:420px;width:100px;height:40px" role="img" aria-label="Line doodle of a needle and thread"></div>

    <div class="photo-strip">
      <div class="photo photo--candles" role="img" aria-label="Photo of decorated candles and cupcakes on a table"></div>
      <div class="photo photo--pinwheels" role="img" aria-label="Photo of colourful paper pinwheels"></div>
      <div class="photo photo--owl" role="img" aria-label="Photo of a decorated turquoise owl figure by a window"></div>
    </div>
    <p class="web">bastuvo-beispiel.com</p>

    <div class="spine">
      <span class="title">FREUDE</span>
      <span class="subtitle">an Kreativität</span>
    </div>

    <div class="front-title"><h1 class="title">FREUDE</h1></div>
    <p class="subtitle front-subtitle">an Kreativität</p>
    <p class="tagline">Plaisir de créer<br>Creative pleasure</p>

    <div class="brand brand--back"><span>BASTUVO</span><span class="mark"></span></div>
    <p class="address">Bastuvo AG · Werkstrasse 7<br>CH-4100 Beispielhausen</p>
    <div class="brand brand--front"><span>BASTUVO</span><span class="mark"></span></div>
  </main>
</body>
</html>
```